2016 Catalog Creative Templates for text pages. Needing updated color pallet and fresh ideas

Adding a few additional comments:
Not too busy on the cover - in other words try to keep consistent and not lots of different ideas going on.

Page numbers - need to not make these large, but keep a readable size.

No need to list product categories on each page, listing once on our tab for the large catalog and this will be listed on the cover for the different books.

We are looking for creative ideas for layout design templates for our upcoming catalogs. In general all of our catalog will follow the same layout template, just slight changes to colors used in each section or catalog. Ideally, I would need one great design for a spread in our books, and a great color pallet for all the other sections and catalogs.
We are a manufacturer of mirrors, art, wall decor, lamps, lighting fixtures, rugs and accent furniture. I will be attaching current catalog layouts for reference. We prefer to keep design fairly simple on the text pages, using neutral colors throughout, this allows for our products to be the main focus in the catalogs. The catalogs that are separate books, we like keeping the color scheme the same as the wall decor book. Meaning using similar, neutral colors and design aspects. We also like to keep items to scale on pages as close as possible, on all of our books.

We have several catalogs, below is a brief description.

Wall Decor book - this is consists of 6 sections. Mirrors, Alternative Wall Decor, Clocks, Art, Accessories and Index, Each are separated by tab pages.
Accent Furniture - throughout this book, we try to use a lot of beauty and detail shots to enhance the beauty of this book, and to show we have other coordinating product. We do this in other books, just not as much. With so many product skews, it makes it very difficult to allow for this in other books.
Lamp Catalog - With this book it's also difficult to use lots of beauty shots as we have so many skews, like to keep scale fairly close on items.
Rug Catalog - sample pages attached
Lighting Catalog - sample attached

Catalog Covers - I have attached a few versions from the past few years. The 2015, the globe on the front isn't printed gray, this was used for placement and size as it was embossed. On the ones with color images, we spot gloss, varnished just the images and printed background with as a matte finish.

Thanks
Megan Pollock
Updates

Adding a few additional comments: Not too busy on the cover - in other words try to keep consistent and not lots of different ideas going on. Page numbers - need to not make these large, but keep a readable size. No need to list product categories on each page, listing once on our tab for the large catalog and this will be listed on the cover for the different books.

Guys, I really am not concerned with the deadline, I would rather get a great catalog design.

Target Market(s)

Wholesale industry customers, designers, etc.

Requirements
Must have
• Must have great, neutral colors, template ideas need to allow for product to be set up to scale.
Should not have
• Bright, neon colors. We generally stick to a neutral color pallet. Open to suggestions of colors, just not too far out of the box.

```html
<!DOCTYPE html>
<html lang="en">
<head>
<meta charset="utf-8">
<title>Introduction — Proposal for Halden Project</title>
<link rel="stylesheet" href="https://fonts.googleapis.com/css2?family=Jost:wght@300;400&family=Lato:wght@400&display=swap">
<style>
  :root {
    --canvas: #ffffff;
    --ink-soft: #7a7d82;
    --ink: #2e2e2e;
    --body-ink: #5a5a5a;
    --guide: #a9d5e8;
    --band: #a9c4d3;
    --accent: #2f9fd6;
    --linen: #f7f5f0;
    --paper: #fafaf8;
    --rule: #8a8a8a;
    --chair-light: #e4ddd0;
    --chair-dark: #6b5a4c;
  }
  * { margin: 0; padding: 0; box-sizing: border-box; }
  html, body { width: 1200px; height: 849px; overflow: hidden; background: var(--canvas); }
  .board { position: relative; width: 1200px; height: 849px; }

  .board-title {
    position: absolute; left: 33px; top: 21px;
    font-family: "Jost", sans-serif; font-weight: 300;
    font-size: 18px; letter-spacing: 12.2px; color: var(--ink-soft);
  }

  .spread {
    position: absolute; left: 320px; top: 285px; width: 560px; height: 378px;
    display: flex;
  }
  .page {
    position: relative; width: 280px; height: 378px;
    border: 1px dashed var(--guide);
  }
  .page--left { background: var(--linen); }
  .page--right {
    background: linear-gradient(to right, var(--linen) 0 62px, var(--paper) 62px);
    border-left: none;
  }

  .product-shot {
    position: absolute; left: 29px; top: 23px; width: 154px; height: 164px;
    background: radial-gradient(ellipse at 60% 45%, var(--chair-light) 0 45%, #b9ae9e 70%, var(--chair-dark) 100%);
    border-radius: 40% 40% 8% 8% / 30% 30% 6% 6%;
  }

  .intro-rule {
    position: absolute; left: 61px; top: 0; width: 2px; height: 248px;
    background: var(--rule);
  }
  .intro-heading {
    position: absolute; left: 69px; top: 40px;
    font-family: "Jost", sans-serif; font-weight: 400;
    font-size: 15px; letter-spacing: 0.3px; color: var(--ink);
  }
  .intro-copy {
    position: absolute; left: 69px; top: 63px; width: 203px;
    font-family: "Lato", sans-serif; font-size: 5.4px; line-height: 13.3px;
    color: var(--body-ink);
  }
  .intro-copy p + p { margin-top: 13.3px; }

  .footer-band {
    position: absolute; left: 0; top: 754px; width: 1200px; height: 4px;
    background: var(--band);
  }
  .studio-mark {
    position: absolute; left: 50px; top: 792px;
    width: 22px; height: 22px; border-radius: 50%;
    background: var(--accent);
  }
  .studio-name {
    position: absolute; left: 106px; top: 803px;
    font-family: "Jost", sans-serif; font-weight: 300;
    font-size: 11px; letter-spacing: 9px; color: var(--ink-soft);
  }
  .project-line {
    position: absolute; left: 759px; top: 781px;
    font-family: "Jost", sans-serif; font-weight: 300;
    font-size: 14px; letter-spacing: 8.3px; color: var(--ink-soft);
    white-space: nowrap;
  }
</style>
</head>
<body>
  <main class="board">
    <h1 class="board-title">INTRODUCTION</h1>

    <section class="spread">
      <div class="page page--left">
        <div class="product-shot" role="img" aria-label="Product photograph: upholstered wingback accent chair in linen with cowhide side panels"></div>
      </div>
      <div class="page page--right">
        <span class="intro-rule"></span>
        <h2 class="intro-heading">INTRODUCTION</h2>
        <div class="intro-copy">
          <p>Every piece in this collection begins with a sketch and ends with careful handwork. Our makers shape frames, carve details and finish each surface by hand, so no two pieces are quite alike. This catalog presents our newest mirrors, lamps, rugs and accent furniture, shown close to scale so you can judge proportion at a glance. Soft neutral tones run through every page, letting the products lead while the layout stays quiet, calm and easy to follow from section to section.</p>
          <p>Each section opens with a tab page and a single accent colour, drawn from stone, linen and driftwood. Page numbers sit small but readable at the outer corner. Lifestyle photographs pair with detail shots to show how pieces work together in a finished room.</p>
        </div>
      </div>
    </section>

    <div class="footer-band"></div>
    <span class="studio-mark"></span>
    <p class="studio-name">ELENA MARSH</p>
    <p class="project-line">PROPOSAL FOR HALDEN PROJECT</p>
  </main>
</body>
</html>
```